Personal Trainer website design

We are working with a personal trainer to design a website. They offer their primary services: Diet Coaching, In-Person Coaching (workouts), and Remote Coaching.
Some sites we like: https://www.mirabelthorne.com, https://kavialune.com/en-us, https://corvexfit.co.uk
Thank you for taking the time to consider designing a website for us. We are web developers based in Stockton, CA USA. Most of our projects go through the same process. Understanding this process may help you win a project with us. We custom-code all of our websites in-house. We don’t have any requirements as to what tools you use for your design, but ask that you follow these guidelines.
IMAGES:
We ask that if you use any images, or icons in the design, have a link to the asset, so we can purchase the image/icon. Most of the designs we submit do not have the customer’s images on them unless they have some great images. Be creative; show us the feeling that you are trying to portray with your image choices. Use any royalty-free site you choose. We subscribe to Quillon and mostly use their images, but are ok to purchase images outside of Quillon.
FONTS:
We ask that you identify the fonts you’re using in the design. This can be done in a message if you want. We typically use Brivane Fonts and Quillon Fonts.
CONTENT:
We're always open to different content and ideas. Often, we submit designs with stock images so that the client can see our vision. We typically go back and take pictures after the website launch to use their images with our vision. Lorem Ipsum is fine for paragraphs, but we ask that you make the Headers with correct English. We want to be able to show the vision and identify the sections of the website.
INSPIRATION:
We try and add a couple of links in the brief of some websites that we like to help you get started in your design.
REVISIONS:
We do not often ask for revisions of the designs unless we see something in the design that may not appeal to the client. If there are slight changes that we want to make, we simply do that in the development process.
FEEDBACK:
We rarely give feedback on designs during the design process. We are working on many website projects and do not have the time to give feedback. We usually respond if your request is well thought out and asks specific questions, but a note asking “feedback, please” usually goes unanswered.
1 page

```html
<!DOCTYPE html>
<html lang="en">
<head>
<meta charset="utf-8">
<title>Zenthrafit – Personal Training</title>
<link href="https://fonts.googleapis.com/css2?family=Oswald:wght@500;600&family=Mulish:wght@400;600;700;800&display=swap" rel="stylesheet">
<style>
:root{
  --olive:#7b8b12;
  --ink:#1f1f1f;
  --body:#4a4a4a;
  --soft:#f4f2f3;
  --footer:#1c1b1b;
  --white:#ffffff;
}
*{margin:0;padding:0;box-sizing:border-box}
html,body{width:1200px;height:3846px;overflow:hidden;background:var(--white)}
body{position:relative;font-family:"Mulish",sans-serif;color:var(--body)}
.abs{position:absolute}
.head{font-family:"Oswald",sans-serif;font-weight:600;color:var(--ink);text-transform:uppercase}
.bar{position:absolute;height:3px;background:var(--olive)}
.btn{position:absolute;background:var(--olive);color:var(--white);font-family:"Mulish",sans-serif;font-weight:800;font-size:11px;letter-spacing:.3px;display:flex;align-items:center;justify-content:center;text-transform:uppercase}
.photo{position:absolute}
.para{position:absolute;font-size:16.5px;line-height:24px;text-align:justify;color:var(--body)}

/* header */
.logo{display:flex;align-items:center;gap:10px;font-family:"Oswald",sans-serif;font-weight:600;font-size:34px;color:var(--ink);letter-spacing:1px}
.logo-dot{width:26px;height:26px;border-radius:50%;background:var(--olive)}
.contact-chip{display:flex;align-items:center;gap:12px}
.chip-icon{width:28px;height:28px;border-radius:50%;background:var(--olive);display:flex;align-items:center;justify-content:center}
.chip-label{font-size:12px;font-weight:600;color:var(--ink);line-height:14px}
.chip-value{font-size:17px;font-weight:700;color:var(--ink);line-height:20px}
.nav{top:83px;left:590px;display:flex;gap:0;font-size:14.5px;font-weight:600;color:var(--ink)}
.nav a{text-decoration:none;color:inherit;position:absolute;white-space:nowrap}
.nav a.active{color:var(--olive)}

/* hero */
.hero{top:124px;left:0;width:1200px;height:501px;background:linear-gradient(100deg,#7a6145 0%,#a58866 30%,#c7bfae 55%,#8d9a86 80%,#5b7062 100%)}
.hero-title{top:232px;left:124px;font-family:"Oswald",sans-serif;font-weight:600;font-size:62px;line-height:72px;color:var(--white);text-transform:uppercase}
.hero-sub{top:393px;left:124px;font-size:17px;font-weight:800;line-height:29px;color:var(--white);text-transform:uppercase}
.hero-btn{top:475px;left:127px;width:133px;height:41px;border:2px solid var(--white);font-size:14px}
.dots{top:576px;left:561px;display:flex;gap:8px}
.dots span{width:8px;height:8px;border-radius:50%;background:#f1f1f1}
.dots span.on{background:var(--olive)}

.section-title{font-size:27px;text-align:center;width:1200px;left:0}

.card-title{font-size:19px;text-align:center;width:297px}
.card-text{font-size:12.5px;line-height:18px;text-align:center;width:250px;color:var(--body)}

.blog-card{position:absolute;top:2969px;width:297px;height:459px;background:var(--white);box-shadow:0 4px 18px rgba(0,0,0,.08)}
.blog-date{position:absolute;top:282px;left:29px;font-size:11.5px;color:var(--ink)}
.blog-title{position:absolute;top:300px;left:29px;font-size:16.5px}
.blog-text{position:absolute;top:337px;left:29px;width:245px;font-size:12px;line-height:18px}

/* footer */
.footer{top:3482px;left:0;width:1200px;height:364px;background:var(--footer);color:var(--white)}
.f-head{position:absolute;font-size:14px;font-weight:800;color:var(--white)}
.f-line{position:absolute;height:2px;background:var(--white)}
.f-text{position:absolute;font-size:12px;line-height:15px;color:var(--white);white-space:nowrap}
.f-icon{position:absolute;width:22px;height:22px;border-radius:50%;background:var(--white);display:flex;align-items:center;justify-content:center}
</style>
</head>
<body>

<!-- Header -->
<div class="abs logo" style="top:48px;left:134px">ZENTHRAFIT<span class="logo-dot"></span></div>

<div class="abs contact-chip" style="top:26px;left:670px">
  <div class="chip-icon"><svg width="14" height="10" viewBox="0 0 14 10"><rect x="0.5" y="0.5" width="13" height="9" fill="#fff"/><path d="M0.5 0.5 L7 5.5 L13.5 0.5" fill="none" stroke="#7b8b12" stroke-width="1.2"/></svg></div>
  <div><div class="chip-label">EMAIL US</div><div class="chip-value">info@zenthrafit.com</div></div>
</div>
<div class="abs contact-chip" style="top:26px;left:895px">
  <div class="chip-icon"><svg width="14" height="14" viewBox="0 0 24 24"><path fill="#fff" d="M6.6 10.8a15.1 15.1 0 0 0 6.6 6.6l2.2-2.2a1 1 0 0 1 1-.25 11.4 11.4 0 0 0 3.6.57 1 1 0 0 1 1 1V20a1 1 0 0 1-1 1A17 17 0 0 1 3 4a1 1 0 0 1 1-1h3.5a1 1 0 0 1 1 1c0 1.25.2 2.45.57 3.57a1 1 0 0 1-.25 1z"/></svg></div>
  <div><div class="chip-label">CALL US</div><div class="chip-value">+1 555 010 2040</div></div>
</div>

<nav class="abs nav" style="left:0;width:1200px">
  <a class="active" style="left:590px">HOME</a>
  <a style="left:669px">ABOUT US</a>
  <a style="left:784px">SERVICES</a>
  <a style="left:893px">BLOG</a>
  <a style="left:976px">CONTACT US</a>
</nav>

<!-- Hero -->
<div class="photo hero" role="img" aria-label="Woman training with battle ropes in a bright gym"></div>
<div class="abs hero-title">In-Person<br>Coaching</div>
<div class="abs hero-sub">Lorem ipsum is simply dummy<br>text of the printing and</div>
<div class="btn hero-btn">Read More</div>
<div class="abs dots"><span></span><span></span><span class="on"></span><span></span><span></span></div>

<!-- Services -->
<div class="abs head section-title" style="top:664px">Our Services</div>
<div class="bar" style="top:718px;left:582px;width:36px"></div>

<div class="photo" style="top:760px;left:134px;width:297px;height:253px;background:linear-gradient(135deg,#3f5a4a,#7a8a5c 50%,#2f3a36)" role="img" aria-label="Two people eating healthy meals after a workout"></div>
<div class="photo" style="top:760px;left:452px;width:297px;height:253px;background:linear-gradient(135deg,#5d6873,#8a95a0 50%,#3c444c)" role="img" aria-label="Group squatting with kettlebells in a gym class"></div>
<div class="photo" style="top:760px;left:770px;width:297px;height:253px;background:linear-gradient(135deg,#4a4a4a,#9a9a9a 50%,#2e2e2e)" role="img" aria-label="Trainer filming a remote workout session"></div>

<div class="abs head card-title" style="top:1040px;left:134px">Diet Coaching</div>
<div class="abs head card-title" style="top:1040px;left:452px">In-Person Coaching</div>
<div class="abs head card-title" style="top:1040px;left:770px">Remote Coaching</div>

<div class="abs card-text" style="top:1081px;left:157px">It is a long established fact that a reader will be distracted by the readable con tent of a page when looking at.</div>
<div class="abs card-text" style="top:1081px;left:475px">It is a long established fact that a reader will be distracted by the readable con tent of a page when looking at.</div>
<div class="abs card-text" style="top:1081px;left:793px">It is a long established fact that a reader will be distracted by the readable con tent of a page when looking at.</div>

<div class="btn" style="top:1155px;left:235px;width:95px;height:32px">Read More</div>
<div class="btn" style="top:1155px;left:553px;width:95px;height:32px">Read More</div>
<div class="btn" style="top:1155px;left:871px;width:95px;height:32px">Read More</div>

<!-- Welcome -->
<div class="abs" style="top:1252px;left:0;width:1200px;height:472px;background:var(--soft)"></div>
<svg class="abs" style="top:1252px;left:0" width="600" height="472" viewBox="0 0 600 472"><path d="M0 0 H340 C600 60 640 400 330 472 H0 Z" fill="#fff"/></svg>
<div class="photo" style="top:1294px;left:164px;width:388px;height:388px;border-radius:50%;background:radial-gradient(circle at 45% 40%,#8b7d70,#4a4038 60%,#2a2420)" role="img" aria-label="Man doing lunges with red kettlebells"></div>

<div class="abs head" style="top:1300px;left:622px;font-size:25px">Welcome to Zenthrafit</div>
<div class="bar" style="top:1354px;left:622px;width:90px"></div>
<div class="para" style="top:1392px;left:622px;width:439px">It is a long established fact that a reader will be distra cted by the readable content of a page when looking at its layout. The point of using Lorem Ipsum is that it has a more-or-less normal distribution of letters, as opposed to using 'Content here, content here', making it look like readable English. Many desktop publishing packages and web page editors now use Lorem Ipsum as their default model text.</div>
<div class="btn" style="top:1616px;left:625px;width:96px;height:31px">Read More</div>

<!-- Feature A -->
<div class="abs head" style="top:1792px;left:133px;font-size:25px;line-height:34px">Lorem ipsum is simply dummy<br>text of the printing</div>
<div class="bar" style="top:1888px;left:133px;width:90px"></div>
<div class="para" style="top:1928px;left:133px;width:386px">It is a long established fact that a reader will be distra cted by the readable content of a page when looking at its layout. The point of using Lorem Ipsum is that it has a more-or-less normal distribution of letters, as opposed to using 'Content here, content here', making it look like readable English. Many desktop publishing packages and web page editors now use Lorem Ipsum as their default model text.</div>
<div class="btn" style="top:2175px;left:136px;width:95px;height:31px">Read More</div>
<div class="photo" style="top:1724px;left:600px;width:600px;height:560px;background:linear-gradient(135deg,#1c2a33,#3e4f59 45%,#11181d)" role="img" aria-label="Athlete doing dips on parallel bars"></div>

<!-- Feature B -->
<div class="photo" style="top:2284px;left:0;width:602px;height:538px;background:linear-gradient(135deg,#6f8c3a,#2f3c44 45%,#1d252b)" role="img" aria-label="Two people holding fresh salad bowls, seen from above"></div>
<div class="abs" style="top:2284px;left:602px;width:598px;height:538px;background:var(--soft)"></div>
<div class="abs head" style="top:2341px;left:678px;font-size:25px;line-height:34px">Lorem ipsum is simply dummy<br>text of the printing</div>
<div class="bar" style="top:2436px;left:678px;width:90px"></div>
<div class="para" style="top:2476px;left:678px;width:386px">It is a long established fact that a reader will be distra cted by the readable content of a page when looking at its layout. The point of using Lorem Ipsum is that it has a more-or-less normal distribution of letters, as opposed to using 'Content here, content here', making it look like readable English. Many desktop publishing packages and web page editors now use Lorem Ipsum as their default model text.</div>
<div class="btn" style="top:2722px;left:681px;width:95px;height:31px">Read More</div>

<!-- Blog -->
<div class="abs head section-title" style="top:2868px">Latest Blog</div>
<div class="bar" style="top:2921px;left:582px;width:36px"></div>

<div class="blog-card" style="left:134px">
  <div class="photo" style="top:0;left:0;width:297px;height:252px;background:linear-gradient(135deg,#3a3a3a,#8a8580 55%,#c9c4bf)" role="img" aria-label="Man lifting dumbbells on a bench"></div>
  <div class="blog-date">25 March 2023</div>
  <div class="head blog-title">Lorem ipsum is simply dummy</div>
  <div class="blog-text">It is a long established fact that a reader will be distracted by the readable con tent of a page when looking at.</div>
  <div class="btn" style="top:401px;left:29px;width:95px;height:31px">Read More</div>
</div>
<div class="blog-card" style="left:452px">
  <div class="photo" style="top:0;left:0;width:297px;height:252px;background:linear-gradient(135deg,#1a1a1a,#6d6d6d 50%,#d5d5d5)" role="img" aria-label="Athlete clapping chalk dust in a dark gym"></div>
  <div class="blog-date">25 March 2023</div>
  <div class="head blog-title">Lorem ipsum is simply dummy</div>
  <div class="blog-text">It is a long established fact that a reader will be distracted by the readable con tent of a page when looking at.</div>
  <div class="btn" style="top:401px;left:29px;width:95px;height:31px">Read More</div>
</div>
<div class="blog-card" style="left:770px">
  <div class="photo" style="top:0;left:0;width:297px;height:252px;background:linear-gradient(135deg,#d8dde2,#3a6fb8 50%,#2a2f36)" role="img" aria-label="Man squatting with a barbell"></div>
  <div class="blog-date">25 March 2023</div>
  <div class="head blog-title">Lorem ipsum is simply dummy</div>
  <div class="blog-text">It is a long established fact that a reader will be distracted by the readable con tent of a page when looking at.</div>
  <div class="btn" style="top:401px;left:29px;width:95px;height:31px">Read More</div>
</div>

<!-- Footer -->
<footer class="abs footer">
  <div class="abs logo" style="top:115px;left:150px;color:var(--white)">ZENTHRAFIT<span class="logo-dot"></span></div>

  <div class="f-head" style="top:40px;left:422px">CONTACT US</div>
  <div class="f-line" style="top:63px;left:422px;width:192px"></div>
  <div class="f-icon" style="top:99px;left:422px"><svg width="10" height="12" viewBox="0 0 10 12"><path d="M5 0a4 4 0 0 0-4 4c0 3 4 8 4 8s4-5 4-8a4 4 0 0 0-4-4z" fill="#7b8b12"/><circle cx="5" cy="4" r="1.4" fill="#fff"/></svg></div>
  <div class="f-text" style="top:103px;left:455px">Merrowdale, CA</div>
  <div class="f-icon" style="top:144px;left:422px"><svg width="11" height="11" viewBox="0 0 24 24"><path fill="#7b8b12" d="M6.6 10.8a15.1 15.1 0 0 0 6.6 6.6l2.2-2.2a1 1 0 0 1 1-.25 11.4 11.4 0 0 0 3.6.57 1 1 0 0 1 1 1V20a1 1 0 0 1-1 1A17 17 0 0 1 3 4a1 1 0 0 1 1-1h3.5a1 1 0 0 1 1 1c0 1.25.2 2.45.57 3.57a1 1 0 0 1-.25 1z"/></svg></div>
  <div class="f-text" style="top:144px;left:455px">Call Us<br>+1 (555) 014-7720</div>
  <div class="f-icon" style="top:196px;left:422px"><svg width="11" height="8" viewBox="0 0 14 10"><rect x="0.5" y="0.5" width="13" height="9" fill="#7b8b12"/><path d="M0.5 0.5 L7 5.5 L13.5 0.5" fill="none" stroke="#fff" stroke-width="1.2"/></svg></div>
  <div class="f-text" style="top:196px;left:455px">E mail Us<br>info@brellowmail.com</div>

  <div class="f-head" style="top:40px;left:733px">MENU</div>
  <div class="f-line" style="top:63px;left:733px;width:106px"></div>
  <div class="f-text" style="top:90px;left:735px">HOME</div>
  <div class="f-text" style="top:112px;left:735px">ABOUT US</div>
  <div class="f-text" style="top:135px;left:735px">SERVICES</div>
  <div class="f-text" style="top:157px;left:735px">BLOG</div>
  <div class="f-text" style="top:179px;left:735px">CONTACT US</div>

  <div class="f-head" style="top:40px;left:963px">FOLLOW US</div>
  <div class="f-line" style="top:63px;left:963px;width:106px"></div>
  <div class="f-icon" style="top:119px;left:962px"><span style="width:8px;height:8px;border-radius:50%;background:var(--olive)"></span></div>
  <div class="f-text" style="top:116px;left:997px">Like us on<br>FRENDLOOP</div>
  <div class="f-icon" style="top:170px;left:962px"><span style="width:8px;height:8px;border-radius:50%;background:var(--olive)"></span></div>
  <div class="f-text" style="top:167px;left:997px">Follow us on<br>CHIRPLINE</div>
  <div class="f-icon" style="top:222px;left:962px"><span style="width:8px;height:8px;border-radius:50%;background:var(--olive)"></span></div>
  <div class="f-text" style="top:219px;left:997px">Follow us on<br>WORKLY</div>

  <div class="abs" style="top:267px;left:133px;width:934px;height:1px;background:#8a8a8a"></div>
  <div class="f-text" style="top:303px;left:0;width:1200px;text-align:center;font-size:11px">Copyright © 2023 All Rights Reserved</div>
</footer>

</body>
</html>
```